Kelvaro.ch is looking for business card letterhead and envelope C5 with WOW effect

We need a strong business card for our company Kelvaro.ch, logo is available. You want a black or dark background on which the logo Stark r% 26 # 252; appears. Letterhead and envelope in C5 format should be in a similar design, but does not have to be We need a strong business card for our company Kelvaro.ch, logo is available. A black or dark background is desired, on which the logo Stark comes across. The letterhead and the envelope in C5 format should have a similar design.

Target Market(s)

Private customers as well as entrepreneurs

Contact Information for Business Card

E-mail: info@kelvaro-example.ch
Web.www.Kelvaro-example.ch
Tel: +41 ( 0 ) 79 482 6037
Adresse:
Lindenweg 14
9406 Tarnbach

Hier kann man Icons verwenden für Email,Tel und Adressse

Font styles to use
Other font styles liked:
• Dubai,bold

Colors

Designer to choose colors to be used in the design.

Requirements
Must have
• WOW effect
Nice to have
• R% 26 # 252; back business card with our service listings. - VEHICLE LABELING - SHOP WINDOW LABELING - STICKERS AND MUCH MORE ... in red color

```html
<!DOCTYPE html>
<html lang="en">
<head>
<meta charset="utf-8">
<title>Kelvaro.ch – Business Card</title>
<link rel="stylesheet" href="https://fonts.googleapis.com/css2?family=Montserrat:wght@700;800&family=Open+Sans:wght@400;600&display=swap">
<style>
  :root {
    --backdrop: #3a342f;
    --card-navy: #15203b;
    --card-navy-light: #22304f;
    --honey: #f7c51e;
    --honey-deep: #e9a90f;
    --white: #ffffff;
    --service-red: #d8202a;
    --rule-gold: #a8893a;
  }
  * { box-sizing: border-box; margin: 0; padding: 0; }
  html, body {
    width: 1200px; height: 930px; overflow: hidden;
    background: var(--backdrop);
  }
  .canvas { position: relative; width: 1200px; height: 930px; }

  .card {
    position: absolute;
    width: 560px; height: 320px;
    border-radius: 22px;
    background: linear-gradient(120deg, var(--card-navy) 0%, var(--card-navy-light) 45%, var(--card-navy) 70%);
    box-shadow: 0 18px 40px rgba(0,0,0,.45);
    overflow: hidden;
    color: var(--white);
    font-family: "Open Sans", sans-serif;
  }
  .card--front { left: 110px; top: 100px; }
  .card--back  { left: 530px; top: 510px; }

  .brand {
    display: flex; align-items: center; gap: 12px;
    font-family: "Montserrat", sans-serif;
    font-weight: 800;
    letter-spacing: 1px;
    color: var(--white);
    text-transform: uppercase;
  }
  .brand__square { width: 18px; height: 18px; background: var(--honey); }

  /* front */
  .card--front .brand { position: absolute; left: 120px; top: 108px; font-size: 40px; }
  .services {
    position: absolute; left: 152px; top: 172px;
    list-style: none; font-size: 13px; letter-spacing: .3px;
    display: grid; grid-template-columns: auto auto; gap: 8px 26px;
    text-transform: uppercase;
  }
  .services li { display: flex; align-items: center; gap: 7px; }
  .services li::before {
    content: ""; width: 6px; height: 6px; border-radius: 50%;
    background: var(--service-red);
  }
  .services li:first-child { grid-column: 1 / 3; }

  /* back */
  .card--back .brand { position: absolute; left: 36px; top: 40px; font-size: 32px; }
  .person { position: absolute; left: 36px; top: 132px; }
  .person__name {
    font-family: "Montserrat", sans-serif; font-weight: 800;
    font-size: 22px; letter-spacing: 1.5px; text-transform: uppercase;
  }
  .person__surname { color: var(--honey); }
  .person__role { font-size: 13px; margin-top: 2px; }
  .rule {
    position: absolute; left: 36px; top: 194px;
    width: 300px; height: 1px; background: var(--rule-gold);
  }
  .contact {
    position: absolute; left: 36px; top: 206px;
    list-style: none; font-size: 13px; line-height: 22px;
  }
  .contact li { display: flex; align-items: center; gap: 10px; }
  .contact__dot { width: 8px; height: 8px; border-radius: 50%; background: var(--honey); }
  .contact__dot--ring { background: none; border: 2px solid var(--honey); }

  .decor-field {
    position: absolute; right: 40px; top: 30px;
    width: 170px; height: 260px; border-radius: 14px;
    background: linear-gradient(160deg, var(--honey) 0%, var(--honey-deep) 100%);
  }
</style>
</head>
<body>
<main class="canvas">

  <section class="card card--front" aria-label="Business card front">
    <div class="brand"><span class="brand__square"></span>Kelvaro.ch</div>
    <ul class="services">
      <li>Stickers and much more</li>
      <li>Vehicle labeling</li>
      <li>Shop window labeling</li>
    </ul>
  </section>

  <section class="card card--back" aria-label="Business card back">
    <div class="brand">Kelvaro.ch</div>
    <div class="person">
      <p class="person__name">Jonas <span class="person__surname">Brenner</span></p>
      <p class="person__role">Director</p>
    </div>
    <div class="rule"></div>
    <ul class="contact">
      <li><span class="contact__dot"></span>+41 ( 0 ) 79 482 6037</li>
      <li><span class="contact__dot"></span>info@kelvaro-example.ch</li>
      <li><span class="contact__dot contact__dot--ring"></span>www.kelvaro-example.ch</li>
      <li><span class="contact__dot contact__dot--ring"></span>Lindenweg 14, 9406 Tarnbach</li>
    </ul>
    <div class="decor-field" role="img" aria-label="Cluster of yellow honeycomb hexagons, filled and outlined"></div>
  </section>

</main>
</body>
</html>
```